Wordpress Design For Financial Investment Company

//** NEW WIREFRAME ADDED TO HELP WITH LAYOUT ISSUES. PLEASE REFER TO WIREFRAME IN ATTACHED FILES. NO DESIGN WILL BE CONSIDERED IF IT DOES NOT FOLLOW THE WIREFRAME. **//
//** PLEASE READ THE ENTIRE BRIEF INCLUDING ALL UPDATES TO THE BRIEF. THE CLIENT IS VERY SPECIFIC ABOUT WHAT THEY WANT AND I'VE COVERED SEVERAL THINGS IN THE UPDATES. THERE IS ALSO A VIDEO UPDATE THAT HAS SOME VALUABLE INFORMATION IN IT FOR THIS CONTEST. **//
The client is an investment advisor who needs a new website designed. The current site is http://www.velmorhold.example.
The client wants the site to be green to match the attached logo.
The home page should have relevant images in the rotator. No people hugging! This is a financial investment site, not a family counseling site.
Also, the client wants 4 buttons on the home page to highlight the 4 main areas they focus on:
Investment Advice and Education
General Financial Planning
Retirement Planning
401K Planning
The top right area of the site needs to have their phone number, a call to action, and 2 buttons.
Their phone number is 303-418-7719
The call to action should say something like "Call for a free consultation!"
The buttons need to say:
Login To Your Brokavell Account
Login To Your Quillbrook Account
The final design should communicate professionalism, financial safety and growth.
Main navigation should be:
Home
About Us
Associates
Services
Contact
Mission Statement (Could also be "Our Mission")
This is a site that the client likes: http://www.pkwadvisoryfirm.example/
Updates
The designs should not have:
Newsletter content. A newsletter sign up is fine
Learning Center
Calculators
Stock prices/tickers
The design should have a contact form on the page.
I have talked to my client and have some updates. I did a video update because I thought it would be easier to show what I'm trying to get across.
Reason: I am going to be extending the contest a few more days. I'm still not getting quite what I want and very few people are even trying to follow the creative brief and the updates to it.
PLEASE read the entire brief and the updates. There is also a video I made that explains everything. I've also attached a wireframe.
Thanks!
Target Market(s)
People looking for a high-end financial investment company.
Industry/Entity Type
Investment
Requirements
Must have
- !!FOLLOW THE WIREFRAME FOR LAYOUT!!
!!THEIR LOGO!!
4 buttons to highlight their main practice areas
Phone number in the top right
"Free Consultation" call to action
2 Login buttons in the top right
A contact form on the page.
Should not have
- The designs should not have:
Learning Center
Calculators
Stock prices/tickers

```html
<!DOCTYPE html>
<html lang="en">
<head>
<meta charset="utf-8">
<title>Velmor Holdings — Home</title>
<link rel="stylesheet" href="https://fonts.googleapis.com/css2?family=Maven+Pro:wght@400;500;600&family=Open+Sans:wght@400;600;700&family=Dancing+Script:wght@700&display=swap">
<style>
:root{
  --page-bg:#6a6a6a;
  --sheet:#ffffff;
  --panel:#f7f8f8;
  --teal:#1aa9a1;
  --teal-dark:#0f8c85;
  --teal-text:#1b8f8a;
  --orange:#f0734a;
  --navy:#3c4a6b;
  --ink:#333a40;
  --muted:#8a8f94;
  --rule:#e3e5e6;
  --footer:#2f3032;
  --footer-bar:#232425;
  --footer-text:#a9abad;
}
*{box-sizing:border-box;margin:0;padding:0}
html,body{width:840px;height:1200px;overflow:hidden}
body{background:var(--page-bg);font-family:"Open Sans",Arial,sans-serif;color:var(--ink);position:relative}
.abs{position:absolute}
.sheet{position:absolute;left:77px;top:28px;width:686px;height:1144px;background:var(--sheet);box-shadow:0 0 6px rgba(0,0,0,.35)}

/* header */
.login-tabs{left:414px;top:30px;width:334px;height:24px;border:1px solid #d9dcdd;border-top:none;border-radius:0 0 4px 4px;display:flex;background:#fff}
.login-tabs a{flex:1;font-size:9px;color:var(--teal-text);text-decoration:none;display:flex;align-items:center;justify-content:center}
.login-tabs a+a{border-left:1px solid #d9dcdd}
.brand{left:112px;top:62px;display:flex;align-items:center;gap:8px}
.brand-dot{width:18px;height:18px;border-radius:50%;background:var(--teal)}
.brand-name{font-family:"Maven Pro",sans-serif;font-weight:500;font-size:20px;color:var(--navy)}
.cta{left:616px;top:74px}
.cta-text{position:absolute;left:30px;top:0;width:120px;font-family:"Maven Pro",sans-serif;font-size:11.5px;line-height:15px;color:var(--navy);letter-spacing:-.2px}
.phone{left:617px;top:106px;font-family:"Maven Pro",sans-serif;font-size:19px;color:#222}

/* nav */
.main-nav{left:69px;top:137px;width:702px;height:33px;background:linear-gradient(#24b5ac,#129e96);box-shadow:0 2px 3px rgba(0,0,0,.25)}
.main-nav a{position:absolute;top:0;line-height:33px;font-size:10.5px;font-weight:600;color:#fff;text-decoration:none;transform:translateX(-50%)}

/* hero */
.hero{left:82px;top:170px;width:676px;height:294px;background:linear-gradient(90deg,#eef2f4 0%,#e6ecef 38%,#c9d0d6 55%,#8a98a8 80%,#3a4d6a 100%)}
.hero-copy{left:96px;top:230px;width:290px}
.hero-title{font-family:"Maven Pro",sans-serif;font-size:22px;line-height:27px;letter-spacing:-.8px;color:#3a3f44}
.hero-title .accent{color:var(--orange)}
.hero-body{margin-top:14px;font-size:8.4px;line-height:14.6px;color:#8a8f94;width:226px;margin-left:2px}
.dots{left:704px;top:472px;display:flex;gap:4px}
.dots i{width:4px;height:4px;border-radius:50%;background:var(--orange)}
.dots i:first-child{background:var(--teal)}

/* practice areas */
.practice{left:82px;top:464px;width:676px;height:187px;background:var(--panel)}
.area-list{left:96px;top:482px;width:188px}
.area-list li{list-style:none;height:37px;line-height:37px;padding-left:26px;font-size:9.5px;font-weight:600;color:var(--teal-text);border-bottom:1px solid var(--rule);position:relative}
.area-list li.active{color:var(--orange);background:#fff;border:1px solid var(--rule);border-right:none;box-shadow:0 1px 2px rgba(0,0,0,.08)}
.area-list li.active::before{content:"";position:absolute;left:10px;top:16px;width:4px;height:4px;border-radius:50%;background:var(--orange)}
.area-list li:last-child{border-bottom:none}
.area-edge{left:282px;top:482px;width:3px;height:148px;background:linear-gradient(90deg,#e2e4e5,transparent)}
.area-title{left:306px;top:494px;font-size:14.5px;font-weight:600;color:var(--teal-dark)}
.area-body{left:311px;top:531px;width:430px;font-size:8.4px;line-height:14.6px;color:var(--muted)}
.view-all{left:318px;top:605px;font-family:"Dancing Script",cursive;font-weight:700;font-size:15px;color:var(--orange)}
.view-rule{left:374px;top:618px;width:302px;height:1px;background:var(--rule)}
.pager{top:610px;width:17px;height:14px;border:1px solid #d8dadb;background:#fff;display:flex;align-items:center;justify-content:center}

/* welcome */
.rule-full{left:82px;width:676px;height:1px;background:var(--rule)}
.welcome-title{left:107px;top:677px;font-family:"Maven Pro",sans-serif;font-size:19px;font-weight:500;color:var(--teal-dark)}
.welcome-body{left:107px;top:714px;width:632px;font-size:8.4px;line-height:14.6px;color:var(--muted)}
.welcome-body a{color:var(--teal-dark);text-decoration:none}

/* columns */
.col-title{top:813px;font-family:"Maven Pro",sans-serif;font-size:15.5px;color:#33383d}
.ql-item{left:104px;display:flex;gap:12px}
.ql-head{font-family:"Maven Pro",sans-serif;font-size:12.5px;color:var(--navy);line-height:16px}
.ql-text{font-size:7.8px;line-height:12.6px;color:var(--muted);width:226px;margin-top:4px}
.more{color:var(--orange);text-decoration:none}
.ql-rule{left:125px;width:236px;height:1px;background:var(--rule)}
.event{left:382px;width:160px;height:54px;border-bottom:1px solid var(--rule);display:flex;gap:10px}
.event-thumb{width:38px;height:38px;border:2px solid #fff;box-shadow:0 0 2px rgba(0,0,0,.3);flex:none}
.event-title{font-size:8.5px;color:var(--orange)}
.event-sub{font-size:7.6px;color:#aaa;margin-top:3px}
.event-date{font-family:Georgia,serif;font-style:italic;font-size:7.8px;color:#888;margin-top:5px}
.news-date{left:562px;top:844px;text-align:center;color:#333}
.news-day{font-family:"Maven Pro",sans-serif;font-size:16px;line-height:16px}
.news-day sup{font-size:7px}
.news-mon{font-family:"Maven Pro",sans-serif;font-size:11px;line-height:12px;color:#555}
.news-yr{font-size:7.5px}
.news-title{left:593px;top:846px;width:120px;font-family:"Maven Pro",sans-serif;font-size:12.5px;line-height:17px;color:var(--navy)}
.news-body{left:592px;top:883px;width:144px;font-size:7.8px;line-height:12.6px;color:var(--muted)}

/* footer */
.footer{left:77px;top:988px;width:686px;height:156px;background:var(--footer)}
.footer-bar{left:77px;top:1144px;width:686px;height:28px;background:var(--footer-bar)}
.f-title{top:1012px;font-family:"Maven Pro",sans-serif;font-size:13px;color:#f0f0f0}
.f-text{font-size:7.6px;line-height:12.4px;color:var(--footer-text);letter-spacing:.3px}
.f-name{color:var(--orange);font-weight:600}
.email-field{left:596px;top:1065px;width:140px;height:21px;background:#fff;border-radius:3px;font-size:7.8px;color:#aaa;line-height:21px;padding-left:9px}
.subscribe{left:598px;top:1100px;width:63px;height:17px;background:linear-gradient(#fff,#dcdcdc);border-radius:2px;font-size:7.8px;font-weight:700;color:#222;text-align:center;line-height:17px}
.copy{left:98px;top:1151px;font-size:8px;color:#ddd}
.foot-nav{right:93px;top:1151px;display:flex;gap:10.5px;font-size:8px;color:#ddd}
</style>
</head>
<body>
<div class="sheet"></div>

<nav class="login-tabs abs">
  <a href="#">Login To Your Brokavell Account</a>
  <a href="#">Login To Your Quillbrook Account</a>
</nav>

<div class="brand abs">
  <span class="brand-dot"></span>
  <span class="brand-name">Velmor Holdings</span>
</div>

<div class="cta abs">
  <svg width="26" height="28" viewBox="0 0 26 28" aria-hidden="true">
    <path d="M4 15 V12 A9 9 0 0 1 22 12 V15" fill="none" stroke="#444" stroke-width="2"/>
    <rect x="1.5" y="13" width="5" height="9" rx="2" fill="#333"/>
    <rect x="19.5" y="13" width="5" height="9" rx="2" fill="#333"/>
    <path d="M6 21 Q8 26 14 26" fill="none" stroke="#444" stroke-width="1.4"/>
    <circle cx="15" cy="26" r="1.6" fill="#333"/>
  </svg>
  <div class="cta-text">Call for a<br>free Consultation !</div>
</div>
<div class="phone abs">303-418-7719</div>

<nav class="main-nav abs">
  <a href="#" style="left:57px">Home</a>
  <a href="#" style="left:150px">About Us</a>
  <a href="#" style="left:265px">Associates</a>
  <a href="#" style="left:378px">Services</a>
  <a href="#" style="left:484px">Contact</a>
  <a href="#" style="left:613px">Mission Statement</a>
</nav>

<div class="hero abs" role="img" aria-label="Photo of a financial advisor meeting a smiling couple at a desk, reviewing documents"></div>
<div class="hero-copy abs">
  <h1 class="hero-title">Only 42% of americans know how much money to save for <span class="accent">RETIREMENT</span>.</h1>
  <p class="hero-body">Le Lorem Ipsum est simplement du faux texte employé dans la composition et la mise en page avant impression. Le Lorem Ipsum est le faux texte standard de l'imprimerie depuis les années 1500.</p>
</div>

<div class="practice abs"></div>
<div class="dots abs"><i></i><i></i><i></i><i></i><i></i></div>
<ul class="area-list abs">
  <li>Investment Advice and Education</li>
  <li class="active">General Financial Planning</li>
  <li>Retirement Planning</li>
  <li>401K Planning</li>
</ul>
<div class="area-edge abs"></div>
<h2 class="area-title abs">General Financial Planning</h2>
<p class="area-body abs">Le Lorem Ipsum est simplement du faux texte employé dans la composition et la mise en page avant impression. Le Lorem Ipsum est le faux texte standard de l'imprimerie depuis les années 1500, quand un peintre anonyme assembla ensemble des morceaux de texte pour réaliser un livre spécimen de polices de texte. Il n'a pas fait que survivre cinq siècles.</p>
<div class="view-all abs">view all</div>
<div class="view-rule abs"></div>
<div class="pager abs" style="left:680px"><svg width="6" height="8" viewBox="0 0 6 8"><path d="M5 1 L1.5 4 L5 7" fill="none" stroke="#555" stroke-width="1.3"/></svg></div>
<div class="pager abs" style="left:702px"><svg width="6" height="8" viewBox="0 0 6 8"><path d="M1 1 L4.5 4 L1 7" fill="none" stroke="#555" stroke-width="1.3"/></svg></div>

<div class="rule-full abs" style="top:651px"></div>
<h2 class="welcome-title abs">WELCOME TO VELMOR</h2>
<p class="welcome-body abs">Le Lorem Ipsum est simplement du faux texte employé dans la composition et la mise en page avant impression. Le Lorem Ipsum est le faux texte standard de l'imprimerie depuis les années 1500, quand un peintre anonyme assembla ensemble des morceaux de texte pour réaliser un livre spécimen de polices de texte. Il n'a pas fait que survivre cinq siècles. mais s'est aussi adapté à la bureautique informatique, sans que son contenu n'en soit modifié. Il a été popularisé dans les années 1960 grâce à la vente de feuilles. <a href="#">Read More</a></p>
<div class="rule-full abs" style="top:791px"></div>

<h3 class="col-title abs" style="left:104px">Quick Links</h3>
<div class="ql-item abs" style="top:846px">
  <svg width="14" height="14" viewBox="0 0 14 14" style="margin-top:2px"><circle cx="7" cy="7" r="7" fill="#3b3d40"/><rect x="3.5" y="6.2" width="7" height="1.6" fill="#fff"/></svg>
  <div>
    <div class="ql-head">Our Firm</div>
    <p class="ql-text">Lorem ipsum dolor sit amet, consectetuer adipiscing elit, sed diam nonummy nibh euismod tincidunt ut laoreet dolore magna aliquam erat volutpat. Ut wisi enim ad minim veniam. <a class="more" href="#">Read More</a></p>
  </div>
</div>
<div class="ql-rule abs" style="top:928px"></div>
<div class="ql-item abs" style="top:934px">
  <svg width="14" height="14" viewBox="0 0 14 14" style="margin-top:2px"><circle cx="7" cy="7" r="7" fill="#3b3d40"/><rect x="3.5" y="6.2" width="7" height="1.6" fill="#fff"/><rect x="6.2" y="3.5" width="1.6" height="7" fill="#fff"/></svg>
  <div class="ql-head" style="font-size:13px">Mission Statement and Core Values</div>
</div>
<div class="ql-rule abs" style="top:958px"></div>

<h3 class="col-title abs" style="left:382px">Events</h3>
<div class="event abs" style="top:850px">
  <div class="event-thumb" role="img" aria-label="Event thumbnail photo" style="background:linear-gradient(#8c8f92,#5d6064)"></div>
  <div><div class="event-title">Anteposuerit litterarum</div><div class="event-sub">est usus legentis in iis.</div><div class="event-date">Jan 07, 2012</div></div>
</div>
<div class="event abs" style="top:905px">
  <div class="event-thumb" role="img" aria-label="Event thumbnail photo" style="background:linear-gradient(#d9cfc4,#b39f8d)"></div>
  <div><div class="event-title">Anteposuerit litterarum</div><div class="event-sub">est usus legentis in iis.</div><div class="event-date">Jan 06, 2012</div></div>
</div>

<h3 class="col-title abs" style="left:560px">Recent News</h3>
<div class="news-date abs">
  <div class="news-day">20<sup>th</sup></div>
  <div class="news-mon">FEB</div>
  <div class="news-yr">2013</div>
</div>
<div class="news-title abs">Vulputate velit esse molestie.</div>
<p class="news-body abs">Lorem ipsum dolor sit consectetuer adipiscing elit, sed diam nonummy nibh euismod tincidunt ut laoreet dolore magna aliquam rat volutpat. Ut wisi enim ad minim, qis nostrud exerci... <a class="more" href="#">&nbsp;Read More</a></p>

<footer>
  <div class="footer abs"></div>
  <h4 class="f-title abs" style="left:104px">Contact Details</h4>
  <div class="f-text abs" style="left:104px;top:1037px">48 Larkspur Court #210<br>Ashford Hills, CO 80942</div>
  <div class="f-text abs" style="left:104px;top:1067px">Phone: 303-418-7719 800-555-0186<br>Fax: 303-555-0142</div>
  <div class="f-text abs" style="left:104px;top:1099px">Harlan @velmorhold.example<br>Map and Directions</div>

  <h4 class="f-title abs" style="left:305px">SiteMap</h4>
  <div class="f-text abs" style="left:305px;top:1037px">Our Associates<br>Our Location<br>Our Services<br>Our Qualifications<br>Our Articles<br>External Page<br>Tell A Friend</div>

  <h4 class="f-title abs" style="left:423px">Testimonials</h4>
  <div class="f-text abs" style="left:424px;top:1036px;width:140px">Lorem Ipsum est simplement du fauxtexte employé.<br><span class="f-name">Corwin Ashdale</span></div>
  <div class="f-text abs" style="left:424px;top:1086px;width:140px">Lorem Ipsum est simplement du fauxtexte employé.<br><span class="f-name">Anonymus</span></div>

  <h4 class="f-title abs" style="left:598px">Sign Up for Newsletter</h4>
  <div class="f-text abs" style="left:597px;top:1035px;width:150px">Lorem Ipsum est simplement du fauxtexte employé</div>
  <div class="email-field abs">Email Address</div>
  <div class="subscribe abs">Subscribe</div>

  <div class="footer-bar abs"></div>
  <div class="copy abs">© Velmor. All rights reserved. Home</div>
  <div class="foot-nav abs"><span>Home</span><span>About Us</span><span>Associates</span><span>Services</span><span>Contact</span><span>Mission Statement</span></div>
</footer>
</body>
</html>
```